Local Roofing Company Billboard Design

We need a billboard design for an 8' x 32' billboard. This billboard would need to be easily readable and stand out well.
I have uploaded a design that we like - simple, readable, and gets the point across. We do NOT want the $1000 off offer included.
We are looking for a black background with white copy so it will stand out. We want the following on the billboard:
Brindlewick Roofing logo
brindlewick-roofing.example (optional)
555.214.7730 (mandatory)
Photo is optional, depends on how it all lays out
Production file must comply with layout requirements (uploaded).
Target Market(s)
Homeowners
Font styles to use
Other font styles liked:
- match font from logo
Colors
Designer to choose colors to be used in the design.
Requirements
Must have
- Black background, white copy, logo must be large and legible. Colors used must match our logo colors.

```html
<!DOCTYPE html>
<html lang="en">
<head>
<meta charset="utf-8">
<title>Brindlewick Roofing Billboard</title>
<link rel="stylesheet" href="https://fonts.googleapis.com/css2?family=Montserrat:wght@400;500;700&display=swap">
<style>
  :root {
    --stage: #8b8c8f;
    --board-black: #060606;
    --white: #ffffff;
    --orange: #e65a25;
    --badge-navy: #213a78;
    --roof-dark: #4a4b57;
    --roof-mid: #7a7b8c;
    --roof-light: #a4a5b4;
  }
  * { margin: 0; padding: 0; box-sizing: border-box; }
  html, body {
    width: 1200px;
    height: 699px;
    overflow: hidden;
  }
  body {
    background: var(--stage);
    font-family: "Montserrat", sans-serif;
    position: relative;
  }
  .billboard {
    position: absolute;
    left: 40px;
    top: 197px;
    width: 1120px;
    height: 305px;
    background: var(--board-black);
    overflow: hidden;
    color: var(--white);
  }
  .billboard__shapes {
    position: absolute;
    inset: 0;
    width: 1120px;
    height: 305px;
  }
  .brand {
    position: absolute;
    left: 54px;
    top: 74px;
    display: flex;
    align-items: center;
    gap: 10px;
    font-size: 21px;
    font-weight: 700;
    line-height: 1;
    color: var(--white);
  }
  .brand__mark {
    width: 16px;
    height: 16px;
    background: var(--orange);
  }
  .tagline {
    position: absolute;
    left: 54px;
    top: 128px;
    line-height: 1;
  }
  .tagline__lead {
    display: block;
    font-size: 38px;
    font-weight: 400;
    color: var(--white);
  }
  .tagline__accent {
    display: block;
    font-size: 38px;
    font-weight: 700;
    color: var(--orange);
    margin-top: -4px;
  }
  .phone {
    position: absolute;
    left: 52px;
    top: 228px;
    font-size: 54px;
    font-weight: 700;
    line-height: 1;
    letter-spacing: -0.5px;
    color: var(--white);
  }
  .website {
    position: absolute;
    left: 483px;
    top: 231px;
    width: 318px;
    height: 47px;
    display: flex;
    align-items: center;
    justify-content: center;
    font-size: 17px;
    font-weight: 500;
    color: var(--white);
  }
</style>
</head>
<body>
  <section class="billboard" aria-label="Brindlewick Roofing billboard">
    <svg class="billboard__shapes" viewBox="0 0 1120 305" aria-hidden="false">
      <defs>
        <linearGradient id="roofTones" x1="0" y1="0" x2="1" y2="1">
          <stop offset="0" stop-color="var(--roof-light)"/>
          <stop offset="0.5" stop-color="var(--roof-mid)"/>
          <stop offset="1" stop-color="var(--roof-dark)"/>
        </linearGradient>
      </defs>
      <polygon class="accent-stripe" points="745,0 760,0 668,305 653,305" fill="var(--orange)"/>
      <polygon class="roof-photo" role="img" aria-label="Aerial photo of a home's grey shingle roof with timber gable trusses"
               points="757,0 1120,0 1120,305 664,305" fill="url(#roofTones)"/>
      <polygon class="corner-accent" points="1120,149 1120,305 1073,305" fill="var(--orange)"/>
      <polygon class="phone-tab" points="0,232 30,232 20,278 0,278" fill="var(--orange)"/>
      <polygon class="certification-badge" role="img" aria-label="Roofing contractor certification badge"
               points="590,34 675,119 590,204 505,119" fill="var(--badge-navy)"/>
      <polygon class="website-frame" points="497,231 801,231 788,278 483,278"
               fill="var(--board-black)" stroke="var(--white)" stroke-width="1.5"/>
    </svg>

    <div class="brand">
      <span class="brand__mark"></span>
      <span class="brand__name">Brindlewick Roofing</span>
    </div>

    <h1 class="tagline">
      <span class="tagline__lead">Quality roofing</span>
      <span class="tagline__accent">you can trust</span>
    </h1>

    <p class="phone">555.214.7730</p>

    <p class="website">brindlewick-roofing.example</p>
  </section>
</body>
</html>
```